Fern Haven Premier Cleaning Service , Inc wants to make the buck so make it happen = )

I need a postcard design for my cleaning company. I have full ownership and 15+ years experience. At this time we take care of residential clients as well as commercial clients. Mainly offices. I do plan to expand my business in the commercial aspect. My experience is that we compete with franchise companies and my company deliveries a higher quality of work.
I already have a logo designed which I would like to use. Basically we do high quality, detail oriented work not just the first time to get the client but years and years ahead.

Target Market(s)

Commercial Offices

Industry/Entity Type

Residential

Font styles to use
Serif
Sans Serif

Colors
9bcb3c
ec1f27
33a6d7
3075b4
f78f20

Requirements
Must have
• focusing on quality, reliability, wants to stand of the crowd
Nice to have
• anything that makes the sale
Should not have
• too much general cleaning company adds

```html
<!DOCTYPE html>
<html lang="en">
<head>
<meta charset="utf-8">
<title>Fern Haven Premier Cleaning Service , Inc — Postcard</title>
<link rel="stylesheet" href="https://fonts.googleapis.com/css2?family=Open+Sans:wght@400;600;700&display=swap">
<style>
  :root {
    --navy: #1f5478;
    --blue: #3075b4;
    --sky: #33a6d7;
    --green: #9bcb3c;
    --red: #ec1f27;
    --orange: #f78f20;
    --ink: #1d4a6e;
    --paper: #ffffff;
    --stage: #eef1f4;
    --box-line: #c9d2da;
    --tag: #a9c4dc;
  }
  * { box-sizing: border-box; margin: 0; padding: 0; }
  html, body { width: 1200px; height: 731px; overflow: hidden; background: var(--stage); }
  body { font-family: "Open Sans", Arial, sans-serif; color: var(--ink); position: relative; }

  .postcard {
    position: absolute; left: 60px; top: 40px; width: 1080px; height: 650px;
    background: var(--paper); overflow: hidden;
    border-top: 5px solid var(--navy);
    box-shadow: 0 6px 18px rgba(0,0,0,.18);
  }
  .commercial-band {
    position: absolute; left: 0; top: 250px; width: 100%; height: 400px;
    background: var(--navy);
  }

  .brand { position: absolute; top: 12px; left: 0; width: 100%; display: flex; justify-content: center; align-items: center; gap: 10px; }
  .brand-dot { width: 28px; height: 28px; border-radius: 50%; background: var(--green); }
  .brand-name { font-size: 18px; font-weight: 600; color: var(--blue); }

  .section-title { position: absolute; left: 0; top: 50px; width: 100%; text-align: center; font-size: 20px; font-weight: 600; color: var(--ink); letter-spacing: .5px; }

  .living-areas { position: absolute; left: 40px; top: 88px; width: 1000px; }
  .living-areas h3 { font-size: 18px; font-weight: 700; color: var(--ink); margin-bottom: 2px; }
  .living-areas p { font-size: 12.5px; line-height: 1.55; }

  .service-box {
    position: absolute; background: var(--paper); border: 2px solid var(--box-line);
    border-radius: 16px; padding: 12px 20px;
  }
  .service-box h3 { font-size: 17px; font-weight: 600; color: var(--green); margin-bottom: 4px; }
  .service-box p { font-size: 12.5px; line-height: 1.6; text-align: justify; }
  .service-box.kitchen { left: 40px; top: 178px; width: 500px; height: 192px; }
  .service-box.bathrooms { left: 570px; top: 168px; width: 470px; height: 166px; }

  .commercial-title { position: absolute; left: 40px; top: 382px; width: 500px; text-align: center; color: var(--paper); font-size: 20px; font-weight: 600; letter-spacing: .5px; }

  .panel { position: absolute; border-radius: 16px; padding: 12px 20px; color: var(--paper); font-size: 12.5px; line-height: 1.6; }
  .panel h4 { display: inline-block; font-size: 13.5px; font-weight: 600; padding: 0 4px; margin-bottom: 4px; }
  .panel.clients { left: 600px; top: 350px; width: 440px; height: 116px; background: var(--green); }
  .panel.clients h4 { background: var(--paper); color: var(--navy); }
  .panel.approach { left: 100px; top: 420px; width: 480px; height: 136px; background: var(--blue); }
  .panel.approach h4 { background: var(--tag); color: var(--navy); }

  .pill { position: absolute; border-radius: 22px; color: var(--paper); font-size: 16px; display: flex; align-items: center; justify-content: center; }
  .pill.email { left: 700px; top: 476px; width: 340px; height: 36px; background: var(--blue); }
  .pill.website { left: 130px; top: 570px; width: 400px; height: 42px; background: var(--green); font-size: 18px; }

  .call-badge {
    position: absolute; left: 590px; top: 524px; width: 260px; height: 260px;
    border-radius: 50%; background: var(--paper); text-align: center; padding-top: 26px;
    color: var(--red);
  }
  .call-badge .label { font-size: 21px; }
  .call-badge .phone { font-size: 22px; font-weight: 600; letter-spacing: .5px; }
</style>
</head>
<body>
  <article class="postcard">
    <div class="commercial-band"></div>

    <header class="brand">
      <span class="brand-dot"></span>
      <span class="brand-name">Fern Haven Premier Cleaning Service , Inc</span>
    </header>
    <h2 class="section-title">RESIDENTIAL CLEANING</h2>

    <section class="living-areas">
      <h3>ALL LIVING AREAS</h3>
      <p>Remove all cobwebs - Clean ceiling fans, dust light fixtures - Clean light switch plates - Clean smudges from doors - Dust blinds, window sills - Dust picture frames, knick-knacks - Dust furniture - Vacuum upholstered furniture - Clean baseboards - Straighten up - Remove trash - Vacuum floors - Mop hard surface areas</p>
    </section>

    <section class="service-box kitchen">
      <h3>KITCHEN</h3>
      <p>Remove cob-webs - Dust ceiling fans, light fixtures - Wipe cabinets and drawers exterior - Clean light switch plates - Remove smudges from doors - Clean blinds and window sills - Counters and backsplash cleaned and sanitized - Sink cleaned and sanitized - Microwave cleaned inside - Clean appliances exterior - Clean stovetop - Clean top of refrigerator - Remove trash, replace liner - Clean baseboards - Vacuum and wash floors</p>
    </section>

    <section class="service-box bathrooms">
      <h3>BATHROOMS</h3>
      <p>Remove cob-webs - Clean light fixtures - Clean light switch plates - Dust, wipe clean towel holders - Shower, sink, tub and tile cleaned and sanitized - Bathroom cabinets exterior wiped clean - All mirrors and glass cleaned - Toilet interior and exterior cleaned and sanitized - Clean baseboards - Vacuum and wash floors</p>
    </section>

    <section class="panel clients">
      <h4>WE PROVIDE SERVICES TO:</h4>
      <p>Apartment Buildings • Professional Offices • Property Management Companies • Realtors • Financial Institutions / Banks • Hair Salons / Nail Salons / Spas</p>
    </section>

    <div class="pill email">Email Us : hello@fernhavenclean.com</div>

    <h2 class="commercial-title">COMMERCIAL CLEANING</h2>

    <section class="panel approach">
      <h4>OUR APPROACH:</h4>
      <p>Providing a fully flexible service • Ensuring constant quality • Concrete service plan • Understanding our customers requirements • Availability to respond to any immediate needs • Periodic phone calls • Personal inspections • Cleaning check list • Environmental friendly products</p>
    </section>

    <div class="pill website">www.fernhavenclean.com</div>

    <div class="call-badge">
      <div class="label">Call Us</div>
      <div class="phone">727-555-0148</div>
    </div>
  </article>
</body>
</html>
```